Stationery Design + Business Cards

Stationary (letterhead as A4 210x297mm and Letter 8.5"x11", preferably both master page + 2nd pages)

Also need business cards, standard size 50x88mm, can be vertical or horizontal.

You can use a front/back design for the business cards, or front only.

Looking at the uploaded file (devank, you already have that), I want it to use the first logo on the list (4 colors).

Alternative, try the grayscale version (second file).

I need the following information on the business card (in no particular order, let me know what you come up with): 

Firstname Lastlame 
Title 

Mobile +1 555-204-7391 

VelaMorn, Inc. 
24851 Birchwood Ridge Passage 
Fernvale, ST 46099 
Tel. +1 555-368-4172 
Fax +1 555-619-0834 

Web: www.velamorn.example 
Twitter: twitter/VelaMorn or @VelaMorn 
Facebook: facebook.com/VelaMorn 

For letterhead, just the company name, address + phone number & fax number 

If you think the phone/fax or something else should not be on the business cards, or something could be missing, let me know.

```html
<!DOCTYPE html>
<html lang="en">
<head>
<meta charset="utf-8">
<title>VelaMorn Business Cards</title>
<link href="https://fonts.googleapis.com/css2?family=Open+Sans:wght@400;600;700&display=swap" rel="stylesheet">
<style>
  :root {
    --stage: #000000;
    --paper: #ffffff;
    --brand-blue: #0e4aa0;
    --wordmark-blue: #1d52a6;
    --accent-orange: #f07a1e;
    --ink-light: #ffffff;
    --label: #ffffff;
  }
  * { margin: 0; padding: 0; box-sizing: border-box; }
  html, body {
    width: 1200px; height: 900px; overflow: hidden;
    background: var(--stage);
    font-family: "Open Sans", Arial, sans-serif;
  }
  .sheet { position: relative; width: 1200px; height: 900px; }
  .label {
    position: absolute; color: var(--label);
    font-weight: 700; font-size: 14px; line-height: 18px; text-align: center; width: 420px;
  }
  .card { position: absolute; overflow: hidden; background: var(--brand-blue); color: var(--ink-light); }
  .card--white { background: var(--paper); }
  .card__top { position: absolute; left: 0; top: 0; width: 100%; background: var(--paper); }
  .wordmark {
    position: absolute; display: flex; align-items: center; gap: 8px;
    color: var(--wordmark-blue); font-weight: 400; white-space: nowrap;
  }
  .wordmark__dot { border-radius: 50%; background: var(--accent-orange); flex: none; }
  .centered { position: absolute; left: 0; width: 100%; text-align: center; }
  .person__name { font-weight: 700; font-size: 13px; line-height: 15px; }
  .person__title { font-weight: 400; font-size: 10.5px; line-height: 14px; }
  .person__mobile { font-weight: 700; font-size: 10.5px; line-height: 14px; }
  .contact-row { position: absolute; display: flex; align-items: stretch; font-weight: 600; font-size: 8.5px; line-height: 12px; white-space: nowrap; }
  .contact-row__web { text-align: right; padding-right: 11px; padding-top: 4px; }
  .contact-row__divider { width: 1px; background: rgba(255,255,255,0.8); }
  .contact-row__address { text-align: left; padding-left: 11px; }
  .small { font-weight: 600; font-size: 8.5px; line-height: 11.5px; white-space: nowrap; }
  .vertical-info { font-weight: 700; font-size: 10.5px; line-height: 14px; white-space: nowrap; }
  .faint-mark { position: absolute; border-radius: 50%; background: rgba(60,140,230,0.45); }
</style>
</head>
<body>
<main class="sheet">

  <div class="label" style="left:27px; top:189px;">Horizontal B. card Front</div>
  <section class="card card--white" style="left:23px; top:215px; width:419px; height:238px;">
    <div class="wordmark" style="left:150px; top:150px; font-size:38px;">
      <span class="wordmark__dot" style="width:40px; height:40px;"></span>VelaMorn
    </div>
  </section>

  <div class="label" style="left:23px; top:465px;">Horizontal B. card Back</div>
  <section class="card" style="left:23px; top:485px; width:419px; height:238px;">
    <span class="faint-mark" style="left:96px; top:44px; width:54px; height:54px;"></span>
    <div class="centered" style="top:74px;">
      <div class="person__name">Firstname Lastname</div>
      <div class="person__title">Title</div>
      <div class="person__mobile">Mobile +1 555-204-7391</div>
    </div>
    <div class="contact-row" style="right:10px; top:174px;">
      <div class="contact-row__web">Web: www.velamorn.example<br>Twitter: twitter/VelaMorn or @VelaMorn<br>Facebook: facebook.com/VelaMorn</div>
      <div class="contact-row__divider"></div>
      <div class="contact-row__address">VelaMorn, Inc.<br>24851 Birchwood Ridge Passage<br>Fernvale, ST 46099<br>Tel. +1 555-368-4172, Fax +1 555-619-0834</div>
    </div>
  </section>

  <div class="label" style="left:488px; top:197px;">Horizontal B. card Front Only</div>
  <section class="card" style="left:488px; top:217px; width:420px; height:238px;">
    <div class="card__top" style="height:78px;"></div>
    <div class="wordmark" style="left:222px; top:24px; font-size:29px;">
      <span class="wordmark__dot" style="width:30px; height:30px;"></span>VelaMorn
    </div>
    <div class="centered" style="top:112px;">
      <div class="person__name">Firstname Lastname</div>
      <div class="person__title">Title</div>
      <div class="person__mobile">Mobile +1 555-204-7391</div>
    </div>
    <div class="contact-row" style="right:28px; top:183px;">
      <div class="contact-row__web">Web: www.velamorn.example<br>Twitter: twitter/VelaMorn or @VelaMorn<br>Facebook: facebook.com/VelaMorn</div>
      <div class="contact-row__divider"></div>
      <div class="contact-row__address">VelaMorn, Inc.<br>24851 Birchwood Ridge Passage<br>Fernvale, ST 46099<br>Tel. +1 555-368-4172, Fax +1 555-619-0834</div>
    </div>
  </section>

  <div class="label" style="left:488px; top:468px;">Horizontal B. card Front Only</div>
  <section class="card" style="left:488px; top:491px; width:420px; height:238px;">
    <div class="card__top" style="height:78px;"></div>
    <div class="wordmark" style="left:222px; top:24px; font-size:29px;">
      <span class="wordmark__dot" style="width:30px; height:30px;"></span>VelaMorn
    </div>
    <div class="centered" style="top:102px;">
      <div class="person__name">Firstname Lastname</div>
      <div class="person__title">Title</div>
      <div class="person__mobile">Mobile +1 555-204-7391</div>
    </div>
    <div class="centered small" style="top:167px;">
      VelaMorn, Inc.<br>24851 Birchwood Ridge Passage, Fernvale, ST 46099<br>Tel. +1 555-368-4172, Fax +1 555-619-0834
    </div>
    <div class="centered small" style="top:207px;">
      Web: www.velamorn.example<br>Twitter: twitter/VelaMorn or @VelaMorn&nbsp;&nbsp;Facebook: facebook.com/VelaMorn
    </div>
  </section>

  <div class="label" style="left:850px; top:247px;">Vertical B. card Front Only</div>
  <section class="card" style="left:940px; top:274px; width:238px; height:419px;">
    <div class="card__top" style="height:161px;"></div>
    <div class="wordmark" style="left:40px; top:93px; font-size:28px;">
      <span class="wordmark__dot" style="width:28px; height:28px;"></span>VelaMorn
    </div>
    <div class="centered" style="top:202px;">
      <div class="person__name">Firstname Lastname</div>
      <div class="person__title">Title</div>
      <div class="person__mobile">Mobile +1 555-204-7391</div>
    </div>
    <div class="centered vertical-info" style="top:284px;">
      VelaMorn, Inc.<br>24851 Birchwood Ridge Passage<br>Fernvale, ST 46099<br>Tel. +1 555-368-4172<br>Fax +1 555-619-0834
    </div>
    <div class="centered small" style="top:369px; line-height:12px;">
      Web: www.velamorn.example<br>Twitter: twitter/VelaMorn or @VelaMorn<br>Facebook: facebook.com/VelaMorn
    </div>
  </section>

</main>
</body>
</html>
```